Heron Property Inspection business card

I am the principal inspector of Heron Property Inspections. I serve Northern Virginia from Winchester to Arlington.Associate, Federated Guild of Dwelling Examiners (FGDE)Graduate, FGDE Home Inspectors CourseNational Association of Home Inspectors ExamI'd like the business card to look more professional than comical.I pulled the attached picture off the web. I'd like to have something like that or an image of a house as my logo on the cards.

Target Market(s)

Persons who recently purchased a home.

Industry/Entity Type

Business

Contact Information for Business Card

Bob AllenBadger Home Inspections, LLC.4455 River RoadBluemont, Virginia 20135cell: 703-231-6680e-mail: tkmarlow@postvale.net

Font styles to use
Serif
Sans Serif

Requirements
Must have
• I'd like to have a logo, something that identifies me as a home inspector. The attached images are something that I'd like to have incorporated into my business card logo.
Nice to have
• I'd like a sketch of a house and/or a magnifying glass showing a house being inspected. The attached images are used as a suggestion only, I do not own the images.
Should not have
• Gimmicky stuff. I want to appear professional and trustworthy.

```html
<!DOCTYPE html>
<html lang="en">
<head>
<meta charset="utf-8">
<title>Heron Property Inspections – Business Card</title>
<link rel="stylesheet" href="https://fonts.googleapis.com/css2?family=Cinzel:wght@400;600&family=Tinos&display=swap">
<style>
  :root {
    --backdrop: #e9e6e1;
    --card-white: #f7f7f7;
    --card-shade: #e2e2e2;
    --brand-blue: #1f3f94;
    --brand-blue-deep: #1a3684;
    --sky-blue: #2f9ad6;
    --ink-navy: #1f3a86;
    --text-light: #eef1fa;
    --icon-cyan: #3fb8e8;
  }
  * { margin: 0; padding: 0; box-sizing: border-box; }
  html, body { width: 1200px; height: 892px; overflow: hidden; }
  body {
    background: var(--backdrop);
    display: flex; align-items: center; justify-content: center;
  }
  .card {
    position: relative;
    width: 980px; height: 560px;
    border-radius: 34px;
    overflow: hidden;
    background: linear-gradient(180deg, var(--card-white) 0%, var(--card-shade) 100%);
    box-shadow: 0 18px 40px rgba(0,0,0,.28);
  }
  .band { position: absolute; background: linear-gradient(180deg, var(--brand-blue) 0%, var(--brand-blue-deep) 100%); }
  .band--lower { left: 0; right: 0; top: 300px; bottom: 0; }
  .band--contact { left: 690px; right: 0; top: 175px; height: 130px; }

  .logo-panel {
    position: absolute; left: 250px; top: 120px; width: 440px; height: 250px;
    background: var(--card-white);
    display: flex; align-items: center; justify-content: center; gap: 16px;
  }
  .logo-mark { width: 22px; height: 22px; border-radius: 50%; background: var(--sky-blue); flex: none; }
  .logo-name {
    font-family: "Cinzel", serif; font-weight: 600;
    color: var(--ink-navy); font-size: 30px; line-height: 1.15;
    text-align: left;
  }

  .contact {
    position: absolute; left: 690px; top: 195px; width: 260px;
    display: flex; flex-direction: column; gap: 14px;
    font-family: "Tinos", serif; color: var(--text-light); font-size: 19px;
  }
  .contact__row { display: flex; justify-content: flex-end; align-items: flex-start; gap: 14px; text-align: right; }
  .contact__icon {
    flex: none; width: 26px; height: 26px; background: #0c1a3e; border-radius: 3px;
    display: flex; align-items: center; justify-content: center;
  }
  .contact__icon svg { width: 18px; height: 18px; }

  .person { position: absolute; left: 80px; bottom: 70px; color: var(--text-light); }
  .person__name { font-family: "Cinzel", serif; font-size: 40px; letter-spacing: 1px; }
  .person__role { font-family: "Tinos", serif; font-size: 20px; margin-top: 2px; padding-left: 30px; }
</style>
</head>
<body>
  <main class="card">
    <div class="band band--lower"></div>
    <div class="band band--contact"></div>

    <div class="logo-panel">
      <span class="logo-mark"></span>
      <div class="logo-name">Heron Property<br>Inspections, LLC</div>
    </div>

    <div class="contact">
      <div class="contact__row">
        <span>703-555-0192</span>
        <span class="contact__icon" aria-label="Phone">
          <svg viewBox="0 0 18 18"><rect x="5" y="2" width="8" height="14" rx="1.5" fill="none" stroke="var(--icon-cyan)" stroke-width="1.6"/><circle cx="9" cy="13.3" r="1" fill="var(--icon-cyan)"/></svg>
        </span>
      </div>
      <div class="contact__row">
        <span>tkmarlow@postvale.net</span>
        <span class="contact__icon" aria-label="Email">
          <svg viewBox="0 0 18 18"><rect x="2" y="4" width="14" height="10" fill="none" stroke="var(--icon-cyan)" stroke-width="1.6"/><path d="M2 4 L9 10 L16 4" fill="none" stroke="var(--icon-cyan)" stroke-width="1.6"/></svg>
        </span>
      </div>
      <div class="contact__row">
        <span>7182 Quarry Lane,<br>Fernhill, Virginia 20148</span>
        <span class="contact__icon" aria-label="Address">
          <svg viewBox="0 0 18 18"><path d="M9 16 C5 11 4 9 4 7 A5 5 0 0 1 14 7 C14 9 13 11 9 16Z" fill="var(--icon-cyan)"/><circle cx="9" cy="7" r="2" fill="#0c1a3e"/></svg>
        </span>
      </div>
    </div>

    <div class="person">
      <div class="person__name">Employee Name</div>
      <div class="person__role">Your Position</div>
    </div>
  </main>
</body>
</html>
```